Business Card Design for a Personal Trainer

I need a business card design for my job as a personal trainer. It should have a unique, modern and exclusive design. On the front there should be only my logo with my name and my job. 0162/3819204 Tobias Lendhart Wiesengrundweg 14 80417 Munich Germany The most important contact information is the web adress. it can be bigger than the rest, but its not necessary. The card should be 8,5cmx5,5cm big. Font: Roboto. Colors: black, white, gray, 56c1ff.

```html
<!DOCTYPE html>
<html lang="de">
<head>
<meta charset="utf-8">
<title>Tobias Lendhart – Personal Trainer Visitenkarte</title>
<link href="https://fonts.googleapis.com/css2?family=Work+Sans:wght@400;500;600&display=swap" rel="stylesheet">
<style>
  :root {
    --stage: #1a1a1a;
    --card-dark: #161616;
    --card-dark-2: #2a2a2a;
    --card-light: #ffffff;
    --ink: #1b1b1b;
    --ink-soft: #3a3a3a;
    --white: #ffffff;
    --muted: #bdbdbd;
  }
  * { margin: 0; padding: 0; box-sizing: border-box; }
  html, body { width: 1200px; height: 900px; overflow: hidden; }
  body {
    background: var(--stage);
    font-family: "Work Sans", Arial, sans-serif;
    position: relative;
  }
  .card {
    position: absolute;
    left: 300px;
    width: 600px;
    height: 388px;
    overflow: hidden;
  }
  .card--front { top: 40px; background: var(--card-dark); }
  .card--back { top: 472px; background: var(--card-light); color: var(--ink); }

  .pattern-area {
    position: absolute; inset: 0;
    background: linear-gradient(135deg, var(--card-dark) 0%, var(--card-dark-2) 55%, var(--card-dark) 100%);
  }

  .wordmark { position: absolute; display: flex; flex-direction: column; align-items: flex-start; }
  .wordmark__name { font-weight: 400; letter-spacing: 0.02em; line-height: 1; white-space: nowrap; }
  .wordmark__role {
    display: flex; align-items: center; width: 100%;
    font-weight: 400; text-transform: uppercase; line-height: 1;
  }
  .wordmark__role::before, .wordmark__role::after {
    content: ""; flex: 1; height: 1px; background: currentColor;
  }
  .wordmark__role span { padding: 0 6px; }

  .card--front .wordmark { left: 150px; top: 205px; color: var(--white); }
  .card--front .wordmark__name { font-size: 32px; }
  .card--front .wordmark__role { font-size: 12px; letter-spacing: 0.32em; margin-top: 4px; }
  .brand-dot {
    position: absolute; left: 532px; top: 218px;
    width: 34px; height: 34px; border-radius: 50%; background: var(--white);
  }

  .card--back .wordmark { left: 30px; top: 30px; color: var(--ink); }
  .card--back .wordmark__name { font-size: 28px; }
  .card--back .wordmark__role { font-size: 11px; letter-spacing: 0.3em; margin-top: 3px; }

  .contact { position: absolute; left: 44px; top: 128px; font-size: 15px; color: var(--ink-soft); line-height: 1.4; }
  .contact__name { font-size: 19px; font-weight: 600; color: var(--ink); letter-spacing: 0.04em; }
  .contact__address { margin-top: 22px; }
  .contact__list { list-style: none; margin-top: 22px; }
  .contact__list li { display: flex; align-items: center; gap: 10px; }
  .contact__list svg { width: 11px; height: 11px; fill: none; stroke: var(--ink-soft); stroke-width: 1.6; }

  .portrait {
    position: absolute; left: 360px; top: 84px; width: 220px; height: 304px;
    background: radial-gradient(ellipse at 50% 70%, #5a5a5a 0%, #6e6e6e 40%, #e9e9e9 72%, #ffffff 100%);
  }
</style>
</head>
<body>
  <section class="card card--front">
    <div class="pattern-area" role="img" aria-label="Dezentes Muster aus wiederholten Markenzeichen auf Schwarz"></div>
    <div class="wordmark">
      <span class="wordmark__name">TOBIAS LENDHART</span>
      <span class="wordmark__role"><span>Personal Trainer</span></span>
    </div>
    <div class="brand-dot"></div>
  </section>

  <section class="card card--back">
    <div class="wordmark">
      <span class="wordmark__name">TOBIAS LENDHART</span>
      <span class="wordmark__role"><span>Personal Trainer</span></span>
    </div>
    <div class="contact">
      <p class="contact__name">TOBIAS LENDHART</p>
      <p class="contact__role">Personal Trainer</p>
      <p class="contact__address">Wiesengrundweg 14<br>80417 München</p>
      <ul class="contact__list">
        <li><svg viewBox="0 0 12 12"><path d="M3 1 L5 3 L4 5 Q5 7 7 8 L9 7 L11 9 L9 11 Q3 10 1 3 Z"/></svg>0162/3819204</li>
        <li><svg viewBox="0 0 12 12"><rect x="1" y="2.5" width="10" height="7"/><path d="M1 2.5 L6 6.5 L11 2.5"/></svg>t.lendhart@mailpost.de</li>
        <li><svg viewBox="0 0 12 12"><circle cx="6" cy="6" r="5"/><path d="M1 6 H11 M6 1 Q3 6 6 11 Q9 6 6 1"/></svg>www.tobiaslendhart.de</li>
      </ul>
    </div>
    <div class="portrait" role="img" aria-label="Schwarzweiß-Porträt des Trainers mit verschränkten Armen"></div>
  </section>
</body>
</html>
```